Bring me business with this creative business card

Design my new business card. I am looking for something different with an impact. People will take a look at this card & they will 1- see how different & creative I am, 2-understand what I do 3- Call me to meet me!

I make videos with a message, testimonials. I am dynamic, fun, creative & human. My new website is in construction but in the meantime you can check this old one: brightpath.ca & another one Tidebloom.com & tidebloom facebook page.
I make videos. sometimes with a cameraman, sometimes with my phone. As an ex Public Relations agent, the message is the most important thing for me. I want to make my clients shine! When they start with me they often remind me of a lamb, when I finish coaching them they are powerful like LIONS! That's why I need a powerful business card!

Target Market(s)

Entrepreneurs, solo entrepreneurs, small & medium companies & start ups. People i will meet while networking. People that need videos on their website & social Networks to get attention, to be visible. men & women. From 35 to 49 years old.
I am an ex Public relations agent. I used to send clients in traditional medias, now with videos they have more chances to be seen on google the new media. I do videos of the president, his team, his loyal clients saying how great the company is & expert videos like series so people can be seen for example every 1 st of every month with a short 2 minute video. Also with my 20 years in marketing & communications I can coach & give tips to anybody who needs it.
Target: anybody who would like my old website brightpath.ca & I also have another website but it will be off line soon: tidebloom.com could give you ideas.

Industry/Entity Type

Communications

Contact Information for Business Card

I am in Montreal,So the business cards have to be the usual size like we have in Montreal: 9 cm x 5 cm
Details:My text: Mathilde Tessier Communication coach/HEAD STORYTELLER. "Crafting stories that sound like you" off: 514-555-0147 cell: 514-555-0183. tidebloom.com
mathilde@tidebloom.com logo facebook, youtube, instagram

Colors
f37122

Requirements
Must have
• Dynamic, happy. Orange. Be creative in the look but NOT the shape of the card. Easy to read. Big enough to read.
Should not have
• No funny shapes: no round, no square, just the usual. I love creative but NOT on shape.

```html
<!DOCTYPE html>
<html lang="en">
<head>
<meta charset="utf-8">
<title>Tidebloom Business Card</title>
<link rel="stylesheet" href="https://fonts.googleapis.com/css2?family=Cinzel:wght@600&family=Roboto:wght@400;500;700&display=swap">
<style>
  :root {
    --backdrop: #262729;
    --card-dark: #1d1e20;
    --brand-orange: #f37122;
    --brand-amber: #f6a21c;
    --sun-yellow: #ffd21a;
    --deep-orange: #ff6a00;
    --ink: #0d0d0d;
    --rule-light: #e9e9e9;
  }
  * { margin: 0; padding: 0; box-sizing: border-box; }
  html, body { width: 1200px; height: 960px; overflow: hidden; }
  body {
    position: relative;
    background: var(--backdrop);
    font-family: "Roboto", Arial, sans-serif;
  }

  .card { position: absolute; width: 600px; height: 350px; }

  /* Front card */
  .card-front {
    left: 322px; top: 102px;
    background: var(--card-dark);
    color: var(--brand-orange);
    text-align: center;
  }
  .brand-dot {
    position: absolute; left: 252px; top: 68px;
    width: 96px; height: 96px; border-radius: 50%;
    background: var(--brand-amber);
  }
  .card-front .wordmark {
    position: absolute; left: 0; right: 0; top: 205px;
    font-family: "Cinzel", Georgia, serif; font-weight: 600;
    font-size: 32px; letter-spacing: 0.5px; line-height: 1;
    color: var(--brand-orange);
  }
  .tagline {
    display: flex; align-items: center; justify-content: center; gap: 8px;
    font-family: "Roboto", Arial, sans-serif; font-size: 14px; line-height: 1;
  }
  .tagline::before, .tagline::after {
    content: ""; width: 30px; height: 1px; background: currentColor;
  }
  .card-front .tagline { position: absolute; left: 0; right: 0; top: 243px; color: var(--brand-amber); }
  .card-front .slogan {
    position: absolute; left: 0; right: 0; top: 262px;
    font-size: 13px; font-weight: 500;
  }
  .social-row {
    position: absolute; left: 166px; top: 303px;
    display: flex; align-items: center; gap: 5px;
  }
  .social-row .rule { width: 90px; height: 1px; background: var(--brand-orange); }
  .social-row .rule.right { width: 100px; background: var(--rule-light); }
  .social-row .dot { width: 22px; height: 22px; border-radius: 50%; background: var(--brand-orange); }

  /* Back card */
  .card-back {
    left: 320px; top: 493px; height: 342px;
    color: var(--ink);
    overflow: hidden;
  }
  .pattern-fill {
    position: absolute; inset: 0;
    background: linear-gradient(160deg, var(--sun-yellow) 0%, #ffb400 35%, var(--deep-orange) 70%, #ff9400 100%);
  }
  .back-brand { position: absolute; right: 40px; top: 36px; text-align: center; width: 216px; }
  .back-brand .wordmark {
    font-family: "Cinzel", Georgia, serif; font-weight: 600;
    font-size: 32px; letter-spacing: 0.5px; line-height: 1;
  }
  .back-brand .tagline { margin-top: 8px; font-size: 13px; }
  .contact-block { position: absolute; left: 33px; top: 172px; }
  .person-name { font-size: 22px; font-weight: 700; line-height: 1; }
  .person-role { font-size: 15px; font-weight: 500; line-height: 19px; margin-top: 6px; }
  .contact-list { list-style: none; margin-top: 4px; font-size: 14px; }
  .contact-list li { display: flex; align-items: center; gap: 8px; height: 19.5px; }
  .contact-list svg { width: 14px; height: 14px; fill: var(--ink); flex: none; }
</style>
</head>
<body>

<section class="card card-front" aria-label="Business card front">
  <div class="brand-dot"></div>
  <h1 class="wordmark">TIDEBLOOM</h1>
  <p class="tagline">1 STORY&nbsp; 1 PURPOSE</p>
  <p class="slogan">Crafting stories that sound like you</p>
  <div class="social-row">
    <span class="rule"></span>
    <span class="dot"></span><span class="dot"></span><span class="dot"></span>
    <span class="rule right"></span>
  </div>
</section>

<section class="card card-back" aria-label="Business card back">
  <div class="pattern-fill" role="img" aria-label="Geometric triangle pattern in yellow and orange"></div>
  <div class="back-brand">
    <h2 class="wordmark">TIDEBLOOM</h2>
    <p class="tagline">1 STORY&nbsp; 1 PURPOSE</p>
  </div>
  <div class="contact-block">
    <h3 class="person-name">MATHILDE T.</h3>
    <p class="person-role">COMMUNICATION COACH<br>HEAD STORYTELLER</p>
    <ul class="contact-list">
      <li><svg viewBox="0 0 24 24"><path d="M6.6 10.8a15.1 15.1 0 0 0 6.6 6.6l2.2-2.2a1 1 0 0 1 1-.25 11.4 11.4 0 0 0 3.6.57 1 1 0 0 1 1 1V20a1 1 0 0 1-1 1A17 17 0 0 1 3 4a1 1 0 0 1 1-1h3.5a1 1 0 0 1 1 1c0 1.25.2 2.45.57 3.57a1 1 0 0 1-.25 1z"/></svg>514-555-0147</li>
      <li><svg viewBox="0 0 24 24"><path d="M7 1h10a2 2 0 0 1 2 2v18a2 2 0 0 1-2 2H7a2 2 0 0 1-2-2V3a2 2 0 0 1 2-2zm0 3v14h10V4zm5 15.5a1 1 0 1 0 0 2 1 1 0 0 0 0-2z"/></svg>514-555-0183.</li>
      <li><svg viewBox="0 0 24 24"><path d="M2 5h20v2l-10 6L2 7zm0 4.3 10 6 10-6V19H2z"/></svg>mathilde@tidebloom.com</li>
      <li><svg viewBox="0 0 24 24"><path d="M12 2a10 10 0 1 0 0 20 10 10 0 0 0 0-20zm-1 17.9A8 8 0 0 1 4.1 10.8L9 15.7v1a2 2 0 0 0 2 2zm6.9-2.5A2 2 0 0 0 16 16h-1v-3a1 1 0 0 0-1-1H8v-2h2a1 1 0 0 0 1-1V7h2a2 2 0 0 0 2-2v-.4a8 8 0 0 1 2.9 12.8z"/></svg>www.tidebloom.com</li>
    </ul>
  </div>
</section>

</body>
</html>
```